Medical Clinic Group Looking for Website Design

We own and operate medical clinics and are looking looking to revamp our website. Our current website is www.brightpathcareclinics.ca We need our website to be more functional, user friendly, and easier to maintain.

```html
<!DOCTYPE html>
<html lang="en">
<head>
<meta charset="utf-8">
<title>Brightpath Care Clinics</title>
<link rel="stylesheet" href="https://fonts.googleapis.com/css2?family=Signika:wght@300;400;600;700&family=Sarabun:wght@300;400&family=Poppins:wght@400;500&display=swap">
<style>
:root{
  --cyan:#36d0dc;
  --ink:#1d1d1d;
  --dark:#141414;
  --grey:#6e6e6e;
  --grey-soft:#d2d2d2;
  --text:#7a7a7a;
  --white:#ffffff;
}
*{margin:0;padding:0;box-sizing:border-box}
html,body{width:1200px;height:2989px;overflow:hidden}
body{font-family:"Signika",sans-serif;background:var(--white);color:var(--ink);position:relative}
.abs{position:absolute}

/* hero */
.hero{position:absolute;left:0;top:0;width:1200px;height:685px;background:linear-gradient(100deg,#151515 0%,#1f1f1f 45%,#2a2a2a 70%,#1a1a1a 100%);overflow:hidden}
.brand{position:absolute;display:flex;align-items:center;gap:14px}
.brand-dot{width:46px;height:46px;border-radius:50%;background:var(--cyan)}
.brand-name{font-family:"Signika",sans-serif;font-weight:400;color:var(--cyan);font-size:34px;letter-spacing:.5px}
.nav{position:absolute;top:36px;left:0;width:1200px;height:30px}
.nav a{position:absolute;color:var(--white);font-size:17px;text-decoration:none;font-weight:400}
.hero-welcome{left:100px;top:168px;font-size:40px;font-weight:400;color:var(--cyan)}
.hero-title{left:100px;top:222px;font-size:44px;font-weight:700;color:var(--cyan);line-height:51px;letter-spacing:.3px}
.hero-copy{left:100px;top:396px;width:390px;font-family:Arial,sans-serif;font-size:15px;line-height:21px;color:var(--white)}
.hero-photo{left:700px;top:100px;width:470px;height:550px;border-radius:60px;background:linear-gradient(135deg,#e3e8ea 0%,#9fb3bb 50%,#3a4850 100%)}
.btn{position:absolute;display:flex;align-items:center;justify-content:center;border-radius:4px;font-family:"Signika",sans-serif;text-decoration:none}
.btn-cyan{background:var(--cyan);color:var(--white)}

/* services */
.services-title{left:0;width:1200px;top:780px;text-align:center;font-size:35px;font-weight:300;color:var(--cyan);letter-spacing:.5px}
.tile{position:absolute;width:220px;text-align:center}
.tile svg{display:block;margin:0 auto}
.tile-label{font-size:21px;font-weight:600;color:var(--ink);margin-top:8px}

/* band */
.band{position:absolute;left:0;top:1581px;width:1200px;height:331px;background:linear-gradient(90deg,#3ad3dd 0%,#31c9d5 40%,#3ad3dd 100%)}
.band-text{position:absolute;left:60px;width:1080px;top:78px;text-align:center;color:var(--white);font-size:28px;font-weight:600;line-height:45px;letter-spacing:-.2px}
.btn-white{background:var(--white);color:var(--cyan);font-weight:600;font-size:21px;box-shadow:0 3px 8px rgba(0,0,0,.12)}

/* about */
.about-frame{left:102px;top:2013px;width:477px;height:436px;background:var(--cyan);border-radius:22px}
.about-photo{left:122px;top:2032px;width:478px;height:436px;border-radius:20px;background:linear-gradient(135deg,#c9d3d8 0%,#7d8a92 45%,#3f4a52 100%);box-shadow:0 10px 25px rgba(0,0,0,.15)}
.about-kicker{left:664px;top:2048px;font-size:34px;font-weight:300;color:var(--cyan)}
.about-title{left:660px;top:2110px;font-size:39px;font-weight:600;color:#555}
.about-copy{left:664px;top:2186px;width:438px;font-family:"Sarabun",sans-serif;font-weight:300;font-size:16.5px;line-height:26px;color:var(--text);text-align:justify}

/* footer */
.footer{position:absolute;left:0;top:2576px;width:1200px;height:413px;background:var(--dark);color:var(--white)}
.f-head{position:absolute;font-size:21px;font-weight:600;color:var(--white)}
.f-list{position:absolute;list-style:none;font-family:"Poppins",sans-serif}
.f-list li{color:var(--white)}
.quick li{font-size:16px;font-weight:500;line-height:26.7px}
.help li{font-size:16.5px;font-weight:400;line-height:33.6px}
.f-sub{left:96px;top:197px;font-family:"Poppins",sans-serif;font-size:17px;line-height:22px}
.f-input{left:96px;top:256px;width:292px;height:47px;border:1px solid #cfcfcf;display:flex;align-items:center;justify-content:space-between;padding:0 12px;font-family:Arial,sans-serif;font-size:12px}
.f-contact{position:absolute;left:882px;display:flex;align-items:flex-start;gap:12px;font-family:"Poppins",sans-serif;font-size:15px;line-height:25px;white-space:nowrap}
.f-rule{left:111px;top:333px;width:978px;height:1px;background:#9a9a9a}
.f-copy{left:0;width:1200px;top:357px;text-align:center;font-family:"Poppins",sans-serif;font-size:18px}
</style>
</head>
<body>

<header class="hero">
  <div class="brand" style="left:102px;top:26px">
    <span class="brand-dot"></span>
    <span class="brand-name">Brightpath Care</span>
  </div>
  <nav class="nav">
    <a style="left:531px">Locations</a>
    <a style="left:642px">For Patients</a>
    <a style="left:771px">For Providers</a>
    <a style="left:907px">About Us</a>
    <a style="left:1015px">Book Online</a>
  </nav>
  <h2 class="abs hero-welcome">Welcome To</h2>
  <h1 class="abs hero-title">SPORTS MEDICINE<br>SERVICES NOW AVAILABLE<br>AT OUR LAKEVIEW LOCATION</h1>
  <p class="abs hero-copy">Brightpath Care Clinics is continually adding and improving our services to provide &nbsp;patients with access to comprehensive care under one roof.</p>
  <a class="btn btn-cyan" style="left:100px;top:499px;width:290px;height:55px;font-size:21px">Download Referral Form</a>
  <div class="abs hero-photo" role="img" aria-label="Therapist assessing a patient's shoulder in a clinic room"></div>
</header>

<section>
  <h2 class="abs services-title">OUR SERVICES</h2>

  <div class="tile" style="left:180px;top:862px">
    <svg width="200" height="236" viewBox="0 0 200 236">
      <rect x="36" y="46" width="128" height="128" rx="22" transform="rotate(45 100 110)" fill="var(--cyan)"/>
      <rect x="36" y="36" width="128" height="128" rx="22" transform="rotate(45 100 100)" fill="#fff" stroke="var(--grey)" stroke-width="5"/>
      <circle cx="100" cy="82" r="18" fill="var(--cyan)"/>
      <path d="M66 132 q0-30 34-30 q34 0 34 30 z" fill="var(--cyan)"/>
    </svg>
    <div class="tile-label">Find a Provider</div>
  </div>

  <div class="tile" style="left:485px;top:862px">
    <svg width="200" height="236" viewBox="0 0 200 236">
      <rect x="36" y="46" width="128" height="128" rx="22" transform="rotate(45 100 110)" fill="var(--grey-soft)"/>
      <rect x="36" y="36" width="128" height="128" rx="22" transform="rotate(45 100 100)" fill="#fff" stroke="var(--grey)" stroke-width="5"/>
      <circle cx="100" cy="75" r="6" fill="var(--grey)"/>
      <path d="M64 120 q0-44 36-44 q36 0 36 44 z" fill="var(--grey)"/>
      <rect x="56" y="124" width="88" height="7" fill="var(--grey)"/>
    </svg>
    <div class="tile-label">Services</div>
  </div>

  <div class="tile" style="left:791px;top:862px">
    <svg width="200" height="236" viewBox="0 0 200 236">
      <rect x="36" y="46" width="128" height="128" rx="22" transform="rotate(45 100 110)" fill="var(--grey-soft)"/>
      <rect x="36" y="36" width="128" height="128" rx="22" transform="rotate(45 100 100)" fill="#fff" stroke="var(--grey)" stroke-width="5"/>
      <circle cx="100" cy="100" r="45" fill="var(--grey)"/>
      <path d="M100 72 v30 h20" fill="none" stroke="#fff" stroke-width="8"/>
    </svg>
    <div class="tile-label">Book an Appointment</div>
  </div>

  <div class="tile" style="left:180px;top:1202px">
    <svg width="200" height="236" viewBox="0 0 200 236">
      <rect x="36" y="46" width="128" height="128" rx="22" transform="rotate(45 100 110)" fill="var(--grey-soft)"/>
      <rect x="36" y="36" width="128" height="128" rx="22" transform="rotate(45 100 100)" fill="#fff" stroke="var(--grey)" stroke-width="5"/>
      <path d="M100 130 c-14-20-26-34-26-50 a26 26 0 0 1 52 0 c0 16-12 30-26 50z" fill="var(--grey)"/>
      <circle cx="100" cy="80" r="10" fill="#fff"/>
      <path d="M78 120 q-18 8-2 16 q24 8 48 0 q16-8-2-16" fill="none" stroke="var(--grey)" stroke-width="6"/>
    </svg>
    <div class="tile-label">Locations</div>
  </div>

  <div class="tile" style="left:485px;top:1202px">
    <svg width="200" height="236" viewBox="0 0 200 236">
      <rect x="36" y="46" width="128" height="128" rx="22" transform="rotate(45 100 110)" fill="var(--grey-soft)"/>
      <rect x="36" y="36" width="128" height="128" rx="22" transform="rotate(45 100 100)" fill="#fff" stroke="var(--grey)" stroke-width="5"/>
      <rect x="64" y="66" width="72" height="92" rx="3" fill="var(--grey)"/>
      <rect x="74" y="74" width="62" height="6" fill="#fff"/>
    </svg>
    <div class="tile-label">Patient Resources</div>
  </div>

  <div class="tile" style="left:791px;top:1202px">
    <svg width="200" height="236" viewBox="0 0 200 236">
      <rect x="36" y="46" width="128" height="128" rx="22" transform="rotate(45 100 110)" fill="var(--grey-soft)"/>
      <rect x="36" y="36" width="128" height="128" rx="22" transform="rotate(45 100 100)" fill="#fff" stroke="var(--grey)" stroke-width="5"/>
      <path d="M70 72 l14-8 14 24-10 8 q6 18 24 28 l8-10 24 14-8 14 q-8 8-20 4 q-36-16-50-52 q-2-12 4-22z" fill="var(--grey)"/>
    </svg>
    <div class="tile-label">Contact Us</div>
  </div>
</section>

<section class="band">
  <div class="abs" role="img" aria-label="Faint anatomy and data backdrop" style="inset:0;background:radial-gradient(ellipse at 45% 60%,rgba(20,120,130,.18),transparent 60%)"></div>
  <p class="band-text">BRIGHTPATH CARE CLINICS IS FOCUSED ON OUR PATIENTS FIRST. CONNECT WITH US TO STAY UP TO DATE WITH CURRENT NEWS AND UPCOMING EVENTS.</p>
  <a class="btn btn-white" style="left:499px;top:196px;width:154px;height:52px">Events</a>
</section>

<section>
  <div class="abs about-frame"></div>
  <div class="abs about-photo" role="img" aria-label="Physiotherapist stretching a patient's leg on a treatment table"></div>
  <h3 class="abs about-kicker">ABOUT US</h3>
  <h2 class="abs about-title">BRIGHTPATH CARE CLINICS</h2>
  <p class="abs about-copy">At Brightpath Care Clinics, work/life balance is at the core of our culture. Our philosophy is simple: we take exceptional care of our people so that they can take exceptional care of our patients. Contact us to find out why so many healthcare providers and medical professionals have chosen to join our team.</p>
  <a class="btn btn-cyan" style="left:664px;top:2380px;width:155px;height:52px;font-size:21px;box-shadow:0 4px 10px rgba(0,0,0,.12)">Read More</a>
</section>

<footer class="footer">
  <div class="brand" style="left:95px;top:56px">
    <span class="brand-dot" style="width:54px;height:54px"></span>
    <span class="brand-name" style="font-size:38px">Brightpath Care</span>
  </div>
  <h4 class="f-head" style="left:96px;top:150px">SUBSCRIBE NEWSLETTER</h4>
  <p class="abs f-sub">Enter your email address<br>to subscribe this</p>
  <div class="abs f-input"><span>Email Address</span>
    <svg width="18" height="18" viewBox="0 0 18 18"><path d="M1 9 17 1 12 17 8 11z" fill="#fff"/></svg>
  </div>

  <h4 class="f-head" style="left:484px;top:62px">QUICK LINK</h4>
  <ul class="f-list quick" style="left:487px;top:108px">
    <li>Locations</li><li>For Patients</li><li>For Providers</li><li>About Us</li><li>Book Online</li>
  </ul>

  <h4 class="f-head" style="left:661px;top:62px">HELP LINKS</h4>
  <ul class="f-list help" style="left:665px;top:103px">
    <li>Terms &amp; Conditions</li><li>Privacy Policy</li><li>About Us</li><li>Support</li>
  </ul>

  <h4 class="f-head" style="left:884px;top:58px">OUR LOCATION</h4>
  <div class="f-contact" style="top:108px">
    <svg width="32" height="32" viewBox="0 0 32 32"><circle cx="16" cy="16" r="14.5" fill="none" stroke="#fff" stroke-width="1.5"/><path d="M16 24c-4-5-6-8-6-11a6 6 0 0 1 12 0c0 3-2 6-6 11z" fill="none" stroke="#fff" stroke-width="1.6"/><circle cx="16" cy="13" r="2" fill="#fff"/></svg>
    <span>1420 Lakeview Ave.<br>Westbrook, ON</span>
  </div>
  <div class="f-contact" style="top:184px">
    <svg width="32" height="32" viewBox="0 0 32 32"><circle cx="16" cy="16" r="14.5" fill="none" stroke="#fff" stroke-width="1.5"/><path d="M11 9l3-1 2 4-2 2q1 3 4 4l2-2 4 2-1 3q-2 2-5 1-7-3-9-9-1-3 2-4z" fill="none" stroke="#fff" stroke-width="1.5"/></svg>
    <span style="padding-top:3px">+1 &nbsp;555.210.4470</span>
  </div>
  <div class="f-contact" style="top:242px;font-size:15.5px">
    <svg width="32" height="32" viewBox="0 0 32 32"><circle cx="16" cy="16" r="14.5" fill="none" stroke="#fff" stroke-width="1.5"/><rect x="9" y="11" width="14" height="10" rx="1.5" fill="none" stroke="#fff" stroke-width="1.5"/><path d="M9 12l7 5 7-5" fill="none" stroke="#fff" stroke-width="1.5"/></svg>
    <span style="padding-top:3px">hello@brightpathcareclinics.ca</span>
  </div>

  <div class="abs f-rule"></div>
  <p class="abs f-copy">© copyrights 2022 Brightpath Care Clinics | &nbsp;All Rights Reserved</p>
</footer>

</body>
</html>
```